Facial Tissue Brand Logo and Design

We would like you to design a Logo for the Facial Tissue Brand "Velora" along with the box design. The pack should indicate the pack size (150 x 2 ply). Also our company logo should be present (attached) along with a barcode. The box size dimensions should be 210mm (L) x 110mm (W) x 70mm (H). We are open to all kinds of nice designs which are attractive but not overdone. Happy designing!

UPDATE:
We appreciate the designs so far... but would also love to see more options in a simple and elegent design style that would look good on a table... please see attached below links for reference purpose:

www.pictovault-example.com/image-photo/cleaning-wipes-isolated-on-white-257770819

www.pictovault-example.com/image-photo/cleaning-wipes-isolated-on-white-155326937

www.pictovault-example.com/image-photo/delicate-female-hands-pulling-tissue-out-1330426586

Happy desgining!

We appreciate the designs so far.. but would like to to see some more options.

```html
<!DOCTYPE html>
<html lang="en">
<head>
<meta charset="utf-8">
<title>Velora Facial Tissue – Box Dieline</title>
<link rel="stylesheet" href="https://fonts.googleapis.com/css2?family=Montserrat:wght@500;600;700&display=swap">
<style>
  :root {
    --page-bg: #ffffff;
    --flap-blue: #458fca;
    --navy: #17467a;
    --brand-navy: #1f4f86;
    --dash: #1d3550;
    --tone-white: #f7f9fd;
    --tone-sky: #c9d9f0;
    --tone-lilac: #cfd1e4;
    --tone-mist: #e6ecf6;
    --window-line: #3c7a5a;
  }
  html, body {
    margin: 0;
    padding: 0;
    width: 1200px;
    height: 671px;
    overflow: hidden;
    background: var(--page-bg);
  }
  .canvas {
    width: 1200px;
    height: 671px;
    display: flex;
    align-items: center;
    justify-content: center;
  }
  .dieline {
    width: 590px;
    height: 641px;
    filter: drop-shadow(8px 8px 6px rgba(0,0,0,0.45));
    font-family: "Montserrat", sans-serif;
  }
  .flap { fill: var(--flap-blue); stroke: var(--dash); stroke-width: 1.2; stroke-dasharray: 4 3; }
  .panel-edge { fill: none; stroke: var(--dash); stroke-width: 1.2; stroke-dasharray: 4 3; }
  .dispenser-window { fill: #ffffff; stroke: var(--window-line); stroke-width: 1.2; stroke-dasharray: 5 4; }
  .product-name { fill: var(--brand-navy); font-weight: 600; letter-spacing: 2px; }
  .brand-name { fill: var(--brand-navy); font-weight: 700; }
  .brand-square { fill: var(--brand-navy); }
  .pack-size { fill: #1b1b1b; font-weight: 500; font-size: 14px; }
  .band-text { fill: #ffffff; font-weight: 600; font-size: 14px; }
  .barcode-label { fill: #ffffff; font-size: 9px; font-weight: 500; }
  .band, .barcode-box { fill: var(--navy); }
</style>
</head>
<body>
<div class="canvas">
  <svg class="dieline" viewBox="0 0 868 942" xmlns="http://www.w3.org/2000/svg">
    <defs>
      <linearGradient id="contourTones" x1="0" y1="0" x2="1" y2="1">
        <stop offset="0" stop-color="var(--tone-white)"/>
        <stop offset="0.14" stop-color="var(--tone-sky)"/>
        <stop offset="0.26" stop-color="var(--tone-white)"/>
        <stop offset="0.38" stop-color="var(--tone-lilac)"/>
        <stop offset="0.5" stop-color="var(--tone-mist)"/>
        <stop offset="0.62" stop-color="var(--tone-sky)"/>
        <stop offset="0.74" stop-color="var(--tone-white)"/>
        <stop offset="0.86" stop-color="var(--tone-lilac)"/>
        <stop offset="1" stop-color="var(--tone-white)"/>
      </linearGradient>
    </defs>

    <!-- sheet -->
    <rect x="0" y="0" width="868" height="942" fill="#ffffff"/>

    <!-- top tuck flap -->
    <polygon class="flap" points="174,50 202,0 668,0 694,50"/>

    <!-- left side flaps -->
    <path class="flap" d="M174,67 H40 Q0,67 0,107 V272 Q0,312 40,312 H174 Z"/>
    <polygon class="flap" points="174,322 0,345 0,476 174,497"/>
    <path class="flap" d="M174,512 H40 Q0,512 0,552 V720 Q0,760 40,760 H174 Z"/>
    <polygon class="flap" points="174,770 0,793 0,942 174,942"/>

    <!-- right side flaps -->
    <path class="flap" d="M694,67 H828 Q868,67 868,107 V272 Q868,312 828,312 H694 Z"/>
    <polygon class="flap" points="694,322 868,345 868,476 694,497"/>
    <path class="flap" d="M694,512 H828 Q868,512 868,552 V720 Q868,760 828,760 H694 Z"/>
    <polygon class="flap" points="694,770 868,793 868,942 694,942"/>

    <!-- main printed panel: contour pattern area -->
    <rect x="174" y="50" width="520" height="892" fill="url(#contourTones)" role="img" aria-label="Flowing topographic contour-line pattern in soft sky blue, lilac grey and white across all box panels"/>
    <rect class="panel-edge" x="174" y="50" width="520" height="892"/>

    <!-- bottom panel (upside down) -->
    <rect class="barcode-box" x="562" y="72" width="112" height="59"/>
    <text class="barcode-label" x="618" y="98" text-anchor="middle" transform="rotate(180 618 101)">bar code</text>
    <text class="product-name" x="441" y="144" font-size="20" text-anchor="middle" transform="rotate(180 441 137)">FACIAL TISSUE</text>
    <g transform="rotate(180 441 196)">
      <rect class="brand-square" x="374" y="185" width="15" height="15"/>
      <text class="brand-name" x="396" y="207" font-size="30">Velora</text>
    </g>

    <!-- long side panel -->
    <rect class="brand-square" x="379" y="400" width="14" height="14"/>
    <text class="brand-name" x="400" y="422" font-size="28">Velora</text>
    <text class="product-name" x="441" y="457" font-size="17" text-anchor="middle">FACIAL TISSUE</text>
    <text class="pack-size" x="214" y="483">150 x 2 ply</text>

    <!-- top panel with dispenser opening -->
    <path class="dispenser-window" d="M290,560 H582 Q598,560 598,576 V691 Q598,707 582,707 H288 Q272,707 272,691 V642 Q295,634 295,620 Q295,608 272,600 V576 Q272,560 290,560 Z"/>
    <rect class="brand-square" x="366" y="617" width="16" height="16"/>
    <text class="brand-name" x="390" y="642" font-size="34">Velora</text>
    <text class="product-name" x="441" y="691" font-size="21" text-anchor="middle">FACIAL TISSUE</text>
    <text class="pack-size" x="585" y="756">150 x 2 ply</text>

    <!-- front long panel -->
    <rect class="brand-square" x="239" y="848" width="13" height="13"/>
    <text class="brand-name" x="259" y="869" font-size="26">Velora</text>
    <text class="product-name" x="297" y="904" font-size="17" text-anchor="middle">FACIAL TISSUE</text>
    <polygon class="band" points="478,889 694,889 694,915 460,915"/>
    <text class="band-text" x="489" y="908">ULTRA SOFT</text>
    <text class="band-text" x="592" y="908">150 x 2 ply</text>
  </svg>
</div>
</body>
</html>
```